Infographic for explaining evidence based medicine

I need 2 diagrams for a talking I am doing later this week . The purpose of the talk is to explain the current approach to evidence based medicine and then the approach of utilising big data. The talk is to doctors who are considered experts in their field. I have attached the layout of the diagrams. Everything on them in italics is just notes. I am really just looking to stylise the people, add in some colours and make it look better than mine. There will be minimal changes.

Target Market(s)

Doctors - considered experts in their field

Industry/Entity Type

Medical And Science

Font styles to use
Serif
Sans Serif

Requirements
Must have
• Quick turn around. Simple design. Needs to make my pictures look better then I have done them.
• Need the colours as described - basicially red, orange and green people

```html
<!DOCTYPE html>
<html lang="en">
<head>
<meta charset="utf-8">
<title>Evidence Based Medicine – Trial Outcomes</title>
<link rel="stylesheet" href="https://fonts.googleapis.com/css2?family=Source+Sans+3:wght@400;600&display=swap">
<style>
  :root {
    --bg: #f4f4f4;
    --good: #0ab51f;
    --mid: #f5a800;
    --bad: #f20000;
    --branch: #b85a4e;
    --pill-green: #1f9e4a;
    --pill-white: #e9e9e9;
    --pill-blue: #2d5fa8;
  }
  html, body {
    margin: 0;
    padding: 0;
    width: 1200px;
    height: 765px;
    overflow: hidden;
    background: var(--bg);
    font-family: "Source Sans 3", sans-serif;
  }
  .infographic { display: block; width: 1200px; height: 765px; }
  .person { rx: 6; }
  .person--good { fill: var(--good); }
  .person--mid { fill: var(--mid); }
  .person--bad { fill: var(--bad); }
  .outcome-small { rx: 4; }
  .branch { fill: none; stroke: var(--branch); stroke-width: 7; stroke-linecap: round; }
  .node { stroke: var(--branch); stroke-width: 3; }
  .node--good { fill: var(--good); }
  .node--mid { fill: var(--mid); }
  .node--bad { fill: var(--bad); }
</style>
</head>
<body>
<svg class="infographic" viewBox="0 0 1200 765" xmlns="http://www.w3.org/2000/svg">
  <defs>
    <linearGradient id="pill-a" x1="0" x2="1" y1="0" y2="0">
      <stop offset="0" stop-color="var(--pill-white)"/>
      <stop offset="0.5" stop-color="var(--pill-white)"/>
      <stop offset="0.5" stop-color="var(--pill-green)"/>
      <stop offset="1" stop-color="var(--pill-green)"/>
    </linearGradient>
    <linearGradient id="pill-b" x1="0" x2="0" y1="0" y2="1">
      <stop offset="0" stop-color="#3f72bd"/>
      <stop offset="1" stop-color="#1f4a8a"/>
    </linearGradient>
    <linearGradient id="avg-a" x1="0" x2="0" y1="0" y2="1">
      <stop offset="0" stop-color="var(--good)"/>
      <stop offset="0.55" stop-color="var(--good)"/>
      <stop offset="0.58" stop-color="var(--mid)"/>
      <stop offset="0.9" stop-color="var(--mid)"/>
      <stop offset="0.92" stop-color="var(--bad)"/>
    </linearGradient>
    <linearGradient id="avg-b" x1="0" x2="0" y1="0" y2="1">
      <stop offset="0" stop-color="var(--good)"/>
      <stop offset="0.15" stop-color="var(--good)"/>
      <stop offset="0.18" stop-color="var(--mid)"/>
      <stop offset="0.9" stop-color="var(--mid)"/>
      <stop offset="0.92" stop-color="var(--bad)"/>
    </linearGradient>
  </defs>

  <!-- Patient population -->
  <g class="population" role="img" aria-label="Population of 24 patient figures coloured green, orange and red">
    <rect class="person person--good" x="74" y="89" width="32" height="88"/>
    <rect class="person person--bad" x="135" y="89" width="32" height="88"/>
    <rect class="person person--mid" x="197" y="89" width="32" height="88"/>
    <rect class="person person--mid" x="259" y="89" width="32" height="88"/>

    <rect class="person person--mid" x="74" y="187" width="32" height="88"/>
    <rect class="person person--good" x="135" y="187" width="32" height="88"/>
    <rect class="person person--mid" x="197" y="187" width="32" height="88"/>
    <rect class="person person--good" x="259" y="187" width="32" height="88"/>

    <rect class="person person--good" x="74" y="282" width="32" height="88"/>
    <rect class="person person--mid" x="135" y="282" width="32" height="88"/>
    <rect class="person person--mid" x="197" y="282" width="32" height="88"/>
    <rect class="person person--good" x="259" y="282" width="32" height="88"/>

    <rect class="person person--mid" x="74" y="381" width="32" height="88"/>
    <rect class="person person--good" x="135" y="381" width="32" height="88"/>
    <rect class="person person--bad" x="197" y="381" width="32" height="88"/>
    <rect class="person person--mid" x="259" y="381" width="32" height="88"/>

    <rect class="person person--mid" x="74" y="489" width="32" height="88"/>
    <rect class="person person--mid" x="135" y="489" width="32" height="88"/>
    <rect class="person person--good" x="197" y="489" width="32" height="88"/>
    <rect class="person person--mid" x="259" y="489" width="32" height="88"/>

    <rect class="person person--good" x="74" y="588" width="32" height="88"/>
    <rect class="person person--mid" x="135" y="588" width="32" height="88"/>
    <rect class="person person--good" x="197" y="588" width="32" height="88"/>
    <rect class="person person--mid" x="259" y="588" width="32" height="88"/>
  </g>

  <!-- Treatments -->
  <rect class="treatment" role="img" aria-label="Green and white capsule, treatment A" x="381" y="192" width="123" height="49" rx="24.5" fill="url(#pill-a)"/>
  <rect class="treatment" role="img" aria-label="Blue capsule, treatment B" x="382" y="551" width="121" height="48" rx="24" fill="url(#pill-b)"/>

  <!-- Outcome branches: treatment A -->
  <g class="outcome-tree">
    <path class="branch" d="M680 103 A111 111 0 0 0 680 325"/>
    <line class="branch" x1="569" y1="214" x2="680" y2="214"/>
    <circle class="node node--good" cx="680" cy="103" r="17"/>
    <circle class="node node--mid" cx="680" cy="214" r="17"/>
    <circle class="node node--bad" cx="680" cy="325" r="17"/>
  </g>

  <!-- Outcome branches: treatment B -->
  <g class="outcome-tree">
    <path class="branch" d="M680 466 A111 111 0 0 0 680 688"/>
    <line class="branch" x1="569" y1="577" x2="680" y2="577"/>
    <circle class="node node--good" cx="680" cy="466" r="17"/>
    <circle class="node node--mid" cx="680" cy="577" r="17"/>
    <circle class="node node--bad" cx="680" cy="688" r="17"/>
  </g>

  <!-- Outcome groups: treatment A -->
  <g role="img" aria-label="Seven patients with a good outcome">
    <rect class="outcome-small person--good" x="763" y="51" width="15" height="42"/>
    <rect class="outcome-small person--good" x="782" y="51" width="15" height="42"/>
    <rect class="outcome-small person--good" x="801" y="51" width="15" height="42"/>
    <rect class="outcome-small person--good" x="821" y="51" width="15" height="42"/>
    <rect class="outcome-small person--good" x="772" y="97" width="15" height="42"/>
    <rect class="outcome-small person--good" x="791" y="97" width="15" height="42"/>
    <rect class="outcome-small person--good" x="811" y="97" width="15" height="42"/>
  </g>
  <g role="img" aria-label="Four patients with a partial outcome">
    <rect class="outcome-small person--mid" x="763" y="192" width="15" height="42"/>
    <rect class="outcome-small person--mid" x="782" y="192" width="15" height="42"/>
    <rect class="outcome-small person--mid" x="801" y="192" width="15" height="42"/>
    <rect class="outcome-small person--mid" x="821" y="192" width="15" height="42"/>
  </g>
  <rect class="outcome-small person--bad" role="img" aria-label="One patient with a poor outcome" x="795" y="310" width="15" height="42"/>

  <!-- Outcome groups: treatment B -->
  <g role="img" aria-label="Two patients with a good outcome">
    <rect class="outcome-small person--good" x="787" y="437" width="15" height="42"/>
    <rect class="outcome-small person--good" x="806" y="437" width="15" height="42"/>
  </g>
  <g role="img" aria-label="Nine patients with a partial outcome">
    <rect class="outcome-small person--mid" x="754" y="534" width="15" height="42"/>
    <rect class="outcome-small person--mid" x="774" y="534" width="15" height="42"/>
    <rect class="outcome-small person--mid" x="794" y="534" width="15" height="42"/>
    <rect class="outcome-small person--mid" x="814" y="534" width="15" height="42"/>
    <rect class="outcome-small person--mid" x="834" y="534" width="15" height="42"/>
    <rect class="outcome-small person--mid" x="763" y="580" width="15" height="42"/>
    <rect class="outcome-small person--mid" x="782" y="580" width="15" height="42"/>
    <rect class="outcome-small person--mid" x="801" y="580" width="15" height="42"/>
    <rect class="outcome-small person--mid" x="821" y="580" width="15" height="42"/>
  </g>
  <rect class="outcome-small person--bad" role="img" aria-label="One patient with a poor outcome" x="795" y="672" width="15" height="42"/>

  <!-- Average patient summaries -->
  <rect class="average-patient" role="img" aria-label="Average patient for treatment A, mostly green with orange and red lower parts" x="1031" y="88" width="72" height="221" rx="14" fill="url(#avg-a)"/>
  <rect class="average-patient" role="img" aria-label="Average patient for treatment B, green head and mostly orange body" x="1031" y="471" width="72" height="221" rx="14" fill="url(#avg-b)"/>
</svg>
</body>
</html>
```